PostCard Design Project

I am making a mailing postcard
I am having the mailing printed using 4 color foil on certain parts.
I am looking for a design that maximizes the foil process where certain parts are done in foil to grab the customers attention (example: if there is a car on the postcard the headlights would be done in foil) .
I am targeting some industries, (auto, real estate, medical, beauty) I would like the post card to have examples of postcard ideas for 2 or 3 of these industries.
specs:
the postcard should be atleast 6.5x9 up to 8.5x11, I don't want to restrict the space for the creative as I don't want everything to look like a huge mess. both sides will be used.
the piece is a direct mail piece so it has to meet requirements of https://www.mailvantor.com/business/pdf/quick-reference-guide.pdf
text will be
"business with no limits, meet mailing with no addresses, gain new customers through "Open Porch Route Drop" reach new customers at their home without needing their address. "
I also want some current print specials I am running included.
-double your order FREE (order 500 business cards and get 1000)
-250 100lb gloss stock brochures 99.00
-business packages (cards, envelopes and letterhead) 299
-1000 flyers 140.40
-5000 postcards 179.99
A list of services
banners
booklets
brochures
business cards
calendars
catalogs
CD/DVD packages
envelopes
event tickets
flyers
hangtags
postcards
posters
presentation folders
rack cards
labels
table tents
window cling and decal
"order 24/7 orders@inkwillow.com" must be included
my logo is InkWillow will be supplied later
ive received some great designs. however Im looking for something a little more modern like some zorvel would put out. if the amount of words is too much please feel free to edit. also an idea i had for the list of services i offer is to have it transparent yet readable as the background of the postcard some small some big but covering the entire backgroud. you can then design on top of that with other thing. just an early morning thought
Reason: I have uploaded a sketch of my idea, please take time to look at it for an accurate depiction of what im looking for. feel free to add elements that make it pop off the page
Reason: We are getting close i will be providing feed back today

```html
<!DOCTYPE html>
<html lang="en">
<head>
<meta charset="utf-8">
<title>InkWillow Mailing Postcard</title>
<link href="https://fonts.googleapis.com/css2?family=Open+Sans:wght@400;600;700&display=swap" rel="stylesheet">
<style>
  :root {
    --page: #e6e6e6;
    --navy-deep: #0b1f4d;
    --navy: #123a7a;
    --blue-bright: #1c82c4;
    --ink-white: #ffffff;
    --stamp-line: #1a1a1a;
    --sample-warm: #f2c94c;
    --sample-cool: #4aa3df;
    --sample-light: #e8eef5;
  }
  * { box-sizing: border-box; margin: 0; padding: 0; }
  html, body {
    width: 1200px; height: 900px; overflow: hidden;
    background: var(--page);
    font-family: "Open Sans", Arial, sans-serif;
  }
  .sheet {
    position: relative; width: 1200px; height: 900px;
    display: flex; gap: 40px; align-items: center; justify-content: center;
  }
  .postcard {
    position: relative; width: 560px; height: 380px; overflow: hidden;
    background: radial-gradient(ellipse at 55% 55%, var(--blue-bright) 0%, var(--navy) 55%, var(--navy-deep) 100%);
    color: var(--ink-white);
    box-shadow: 0 4px 14px rgba(0,0,0,.25);
  }
  .mosaic-band {
    position: absolute; left: 0; width: 100%; height: 26px;
    background: linear-gradient(90deg, #e53935, #fb8c00, #fdd835, #43a047, #00acc1, #1e88e5, #8e24aa, #d81b60, #6d4c41, #7cb342, #29b6f6, #f06292, #e53935);
    opacity: .9;
  }
  .mosaic-band--top { top: 0; }
  .mosaic-band--bottom { bottom: 0; }

  .headline {
    position: absolute; top: 36px; left: 20px; right: 20px;
    text-align: center; font-weight: 700; font-size: 15px; line-height: 1.35;
  }
  .sample-fan {
    position: absolute; left: 24px; top: 118px; width: 250px; height: 190px;
    background: linear-gradient(135deg, var(--sample-light) 0%, var(--sample-cool) 45%, var(--sample-warm) 100%);
    border-radius: 4px; transform: rotate(-6deg);
  }
  .sample-fan--small {
    left: 370px; top: 108px; width: 150px; height: 64px;
    background: linear-gradient(120deg, var(--sample-cool), var(--sample-light) 60%, #d6336c);
    transform: rotate(4deg);
  }
  .specials {
    position: absolute; left: 300px; top: 190px; list-style: none;
    font-weight: 600; font-size: 11px; line-height: 1.45;
  }
  .tick-list li { position: relative; padding-left: 15px; }
  .tick-list li::before {
    content: ""; position: absolute; left: 2px; top: .35em;
    width: 4px; height: 8px;
    border-right: 2px solid var(--ink-white); border-bottom: 2px solid var(--ink-white);
    transform: rotate(45deg);
  }
  .tick-list li.note::before { display: none; }
  .order-line {
    position: absolute; bottom: 36px; font-weight: 600; font-size: 15px;
  }
  .postcard--front .order-line { left: 24px; }
  .postcard--back .order-line { right: 24px; }

  .postage-stamp {
    position: absolute; top: 40px; right: 28px; width: 62px; height: 42px;
    background: var(--ink-white); border: 1px solid var(--stamp-line);
    color: var(--stamp-line); font-size: 10px; line-height: 1.2;
    display: flex; align-items: center; justify-content: center; text-align: center;
  }
  .services-title {
    position: absolute; left: 190px; top: 118px; font-weight: 600; font-size: 19px;
  }
  .services {
    position: absolute; list-style: none; font-weight: 600; font-size: 15px; line-height: 1.55;
  }
  .services li { padding-left: 17px; }
  .services--a { left: 36px; top: 196px; }
  .services--b { left: 200px; top: 156px; }
  .services--c { left: 380px; top: 96px; }
</style>
</head>
<body>
<main class="sheet">
  <section class="postcard postcard--front" aria-label="Postcard front">
    <div class="mosaic-band mosaic-band--top" role="img" aria-label="Band of multicoloured print-swatch squares"></div>
    <p class="headline">“ Business with no limits, meet mailing with no addresses,<br>Gain new customers through “Open Porch Route Drop”<br>Reach new customers at their home without needing their address. ”</p>
    <div class="sample-fan" role="img" aria-label="Fanned stack of printed flyers and brochures"></div>
    <div class="sample-fan sample-fan--small" role="img" aria-label="Fan of printed business cards"></div>
    <ul class="specials tick-list">
      <li>Double your order FREE</li>
      <li class="note">(order 500 business cards and get 1000)</li>
      <li>250 100lb gloss stock brochures 99.00</li>
      <li>Business packages</li>
      <li class="note">(cards, envelopes and letterhead) 299</li>
      <li>1000 flyers 140.40</li>
      <li>5000 postcards 179.99</li>
    </ul>
    <p class="order-line">order 24/7 orders@inkwillow.com</p>
    <div class="mosaic-band mosaic-band--bottom" role="img" aria-label="Band of multicoloured print-swatch squares"></div>
  </section>

  <section class="postcard postcard--back" aria-label="Postcard back">
    <div class="mosaic-band mosaic-band--top" role="img" aria-label="Band of multicoloured print-swatch squares"></div>
    <div class="postage-stamp">Postage<br>Stamp</div>
    <h2 class="services-title">Our Services Are</h2>
    <ul class="services services--a tick-list">
      <li>banners</li><li>booklets</li><li>brochures</li>
      <li>business cards</li><li>calendars</li><li>catalogs</li>
    </ul>
    <ul class="services services--b tick-list">
      <li>CD/DVD packages</li><li>envelopes</li><li>event tickets</li>
      <li>flyers</li><li>hangtags</li><li>postcards</li>
    </ul>
    <ul class="services services--c tick-list">
      <li>posters</li><li>presentation folders</li><li>rack cards</li>
      <li>labels</li><li>table tents</li><li>window cling and decal</li>
    </ul>
    <p class="order-line">order 24/7 orders@inkwillow.com</p>
    <div class="mosaic-band mosaic-band--bottom" role="img" aria-label="Band of multicoloured print-swatch squares"></div>
  </section>
</main>
</body>
</html>
```